Vortaleen - Lead the Way!

Vortaleen is a new Silicon Valley company, of the pimrela founders from Berlin, which provides a "Shared Hive Circle". This platform allows the crowd to support startups with money, experts and fame. Our Vision is, that everyone should become an entrepreneur.

Pls find all brief details in the attached document
Updates

Would be nice to have a list of more social services I'm available on, like a list of pictograms of all my services:

Find me on: chattro, fennwix+, qrt, mivrel, datebloom, pohk, rplex, etc...

pls make sure to use the right font:
http://www.typelarder-demo.com/fonts/Orbitron

Target Market(s)

Main target market is those already involved in the startup industry, by fundraising, investing, advising, cofounding and working. Vortaleen brings a totaly new transparency and collaborative way of starting companies to that business.

· Entrepreneurs (looking for funding, team and community)
· Investors (looking for hot investments and )
· Experts (workers looking for startups they can work for equity)
· Incubators & Business Schools (looking for tools to advise startups)

Industry/Entity Type

It Company

Requirements
Must have
• Pls find all brief details in the attached document
Nice to have

```html
<!DOCTYPE html>
<html lang="en">
<head>
<meta charset="utf-8">
<title>Vortaleen – Business Cards</title>
<link rel="stylesheet" href="https://fonts.googleapis.com/css2?family=Arimo:wght@400;700&display=swap">
<style>
  :root {
    --board: #6b7475;
    --card-light: #eceded;
    --card-mid: #d6d8d9;
    --card-dark: #c3c6c7;
    --cyan: #3fcfe3;
    --white: #ffffff;
    --ink: #111111;
    --ink-soft: #3a3a3a;
    --ink-muted: #555b5d;
    --mark-dark: #1c1c1c;
  }
  * { box-sizing: border-box; margin: 0; padding: 0; }
  html, body {
    width: 1200px; height: 2857px; overflow: hidden;
    background: var(--board);
    font-family: "Arimo", Arial, sans-serif;
  }
  .sheet { position: relative; width: 1200px; height: 2857px; }

  .section-title {
    position: absolute; left: 0; width: 1200px; text-align: center;
    color: var(--white); font-weight: 700; font-size: 36px; line-height: 40px;
    letter-spacing: 0.4em; text-indent: 0.4em;
  }

  .card {
    position: absolute; left: 71px; width: 1058px; height: 609px; overflow: hidden;
    background: radial-gradient(ellipse at 55% 45%, var(--card-light) 0%, var(--card-mid) 55%, var(--card-dark) 100%);
  }
  .card-texture {
    position: absolute; inset: 0;
    background: linear-gradient(135deg, rgba(255,255,255,0.18), rgba(180,184,186,0.25) 50%, rgba(255,255,255,0.12));
  }
  .accent { position: absolute; }
  .accent--cyan { background: var(--cyan); }
  .accent--white { background: var(--white); }

  .card-url {
    position: absolute; left: 262px; width: 350px; text-align: center;
    top: 39px; line-height: 24px; color: var(--cyan); font-weight: 700; font-size: 19px; letter-spacing: 0.2em;
  }
  .brand-name {
    position: absolute; left: 50px; top: 56px;
    font-weight: 700; font-size: 110px; line-height: 1; color: var(--ink);
    letter-spacing: -0.02em;
  }
  .brand-tagline {
    position: absolute; left: 537px; top: 148px; line-height: 28px;
    font-weight: 700; font-size: 26px; color: var(--ink-soft);
  }

  .identity { position: absolute; right: 404px; top: 430px; text-align: right; }
  .identity-name { font-weight: 700; font-size: 36px; line-height: 40px; color: var(--cyan); }
  .identity-role { font-weight: 700; font-size: 19px; line-height: 20px; color: var(--ink-soft); }

  .contact-list { position: absolute; list-style: none; }
  .contact-list--direct { left: 400px; top: 497px; }
  .contact-list--social { left: 674px; top: 460px; }
  .contact-item {
    display: flex; align-items: center; gap: 12px;
    height: 40px; font-size: 20px; color: var(--ink-soft); white-space: nowrap;
  }
  .contact-icon { width: 26px; height: 20px; flex: none; }
  .network-chip { width: 22px; height: 22px; background: var(--mark-dark); flex: none; }

  /* back side */
  .offer-heading { position: absolute; left: 186px; top: 91px; line-height: 24px; font-weight: 700; font-size: 21px; color: var(--ink); }
  .offer-list { position: absolute; left: 300px; top: 119px; font-size: 18px; color: var(--ink-soft); line-height: 23px; }
  .offer-join { position: absolute; left: 186px; top: 194px; line-height: 24px; font-weight: 700; font-size: 20px; color: var(--ink); }
  .offer-join span { color: var(--cyan); }
  .notes-list { position: absolute; left: 414px; top: 239px; width: 430px; font-size: 17px; color: var(--ink-soft); line-height: 23px; }
  .notes-list li { display: flex; gap: 6px; }
  .notes-list li::before { content: "\2022"; position: absolute; left: -16px; }
  .notes-line { flex: 1; border-bottom: 1px dashed var(--ink-muted); margin-bottom: 6px; }
  .company-line { position: absolute; left: 186px; top: 364px; line-height: 26px; font-weight: 700; font-size: 22px; color: var(--cyan); }
  .company-line span { color: var(--ink); }
  .company-address { position: absolute; left: 186px; top: 392px; font-size: 21px; color: var(--ink-muted); line-height: 28px; }
  .back-url {
    position: absolute; left: 0; width: 1058px; top: 497px; line-height: 34px; text-align: center;
    font-weight: 700; font-size: 30px; letter-spacing: 0.38em; text-indent: 0.38em; color: var(--cyan);
  }
</style>
</head>
<body>
<main class="sheet">

  <h1 class="section-title" style="top:69px">3 FRONT SIDE</h1>

  <!-- front: Marten Oswig -->
  <section class="card card--front" style="top:123px">
    <div class="card-texture" role="img" aria-label="Faint pixel-creature pattern background"></div>
    <div class="accent accent--cyan" style="left:449px;top:0;width:565px;height:40px"></div>
    <div class="accent accent--white" style="left:1014px;top:20px;width:44px;height:76px"></div>
    <div class="accent accent--cyan" style="left:0;top:434px;width:40px;height:175px"></div>
    <div class="accent accent--white" style="left:40px;top:514px;width:20px;height:95px"></div>
    <p class="card-url">WWW.VORTALEEN.COM</p>
    <p class="brand-name">VORTALEEN</p>
    <p class="brand-tagline">LEAD THE WAY!</p>
    <div class="identity">
      <p class="identity-name">Marten Oswig</p>
      <p class="identity-role">Founder and CTO</p>
    </div>
    <ul class="contact-list contact-list--direct">
      <li class="contact-item"><svg class="contact-icon" viewBox="0 0 26 20"><rect x="1" y="2" width="24" height="16" fill="#1c1c1c"/><path d="M1 2 L13 11 L25 2" stroke="#d6d8d9" stroke-width="2" fill="none"/></svg>Mos@vortaleen.com</li>
      <li class="contact-item"><svg class="contact-icon" viewBox="0 0 26 20"><rect x="7" y="0" width="12" height="20" rx="2" fill="#1c1c1c"/><rect x="9" y="3" width="8" height="11" fill="#d6d8d9"/></svg>000.000.0000</li>
    </ul>
    <ul class="contact-list contact-list--social">
      <li class="contact-item"><span class="network-chip"></span>kinloop.com/martenoswig</li>
      <li class="contact-item"><span class="network-chip"></span>chirpa.com/martenoswig</li>
      <li class="contact-item"><span class="network-chip"></span>worklane.com/martenoswig</li>
    </ul>
  </section>

  <!-- front: Jonas Vellrath -->
  <section class="card card--front" style="top:774px">
    <div class="card-texture" role="img" aria-label="Faint pixel-creature pattern background"></div>
    <div class="accent accent--cyan" style="left:449px;top:0;width:565px;height:40px"></div>
    <div class="accent accent--white" style="left:1014px;top:20px;width:44px;height:76px"></div>
    <div class="accent accent--cyan" style="left:0;top:434px;width:40px;height:175px"></div>
    <div class="accent accent--white" style="left:40px;top:514px;width:20px;height:95px"></div>
    <p class="brand-name">VORTALEEN</p>
    <p class="brand-tagline">LEAD THE WAY!</p>
    <div class="identity">
      <p class="identity-name">Jonas Vellrath</p>
      <p class="identity-role">Founder and CTO</p>
    </div>
    <ul class="contact-list contact-list--direct">
      <li class="contact-item"><svg class="contact-icon" viewBox="0 0 26 20"><rect x="1" y="2" width="24" height="16" fill="#1c1c1c"/><path d="M1 2 L13 11 L25 2" stroke="#d6d8d9" stroke-width="2" fill="none"/></svg>Jve@vortaleen.com</li>
      <li class="contact-item"><svg class="contact-icon" viewBox="0 0 26 20"><rect x="7" y="0" width="12" height="20" rx="2" fill="#1c1c1c"/><rect x="9" y="3" width="8" height="11" fill="#d6d8d9"/></svg>000.000.0000</li>
    </ul>
    <ul class="contact-list contact-list--social">
      <li class="contact-item"><span class="network-chip"></span>kinloop.com/jonasvellrath</li>
      <li class="contact-item"><span class="network-chip"></span>chirpa.com/jonasvellrath</li>
      <li class="contact-item"><span class="network-chip"></span>worklane.com/jonasvellrath</li>
    </ul>
  </section>

  <!-- front: Henrik Albers -->
  <section class="card card--front" style="top:1429px">
    <div class="card-texture" role="img" aria-label="Faint pixel-creature pattern background"></div>
    <div class="accent accent--cyan" style="left:449px;top:0;width:565px;height:40px"></div>
    <div class="accent accent--white" style="left:1014px;top:20px;width:44px;height:76px"></div>
    <div class="accent accent--cyan" style="left:0;top:434px;width:40px;height:175px"></div>
    <div class="accent accent--white" style="left:40px;top:514px;width:20px;height:95px"></div>
    <p class="card-url">WWW.VORTALEEN.COM</p>
    <p class="brand-name">VORTALEEN</p>
    <p class="brand-tagline">LEAD THE WAY!</p>
    <div class="identity">
      <p class="identity-name">Henrik Albers</p>
      <p class="identity-role">Founder and CTO</p>
    </div>
    <ul class="contact-list contact-list--direct">
      <li class="contact-item"><svg class="contact-icon" viewBox="0 0 26 20"><rect x="1" y="2" width="24" height="16" fill="#1c1c1c"/><path d="M1 2 L13 11 L25 2" stroke="#d6d8d9" stroke-width="2" fill="none"/></svg>Hal@vortaleen.com</li>
      <li class="contact-item"><svg class="contact-icon" viewBox="0 0 26 20"><rect x="7" y="0" width="12" height="20" rx="2" fill="#1c1c1c"/><rect x="9" y="3" width="8" height="11" fill="#d6d8d9"/></svg>000.000.0000</li>
    </ul>
    <ul class="contact-list contact-list--social">
      <li class="contact-item"><span class="network-chip"></span>kinloop.com/henrikalbers</li>
      <li class="contact-item"><span class="network-chip"></span>chirpa.com/henrik_albers</li>
      <li class="contact-item"><span class="network-chip"></span>worklane.com/henrikalbers</li>
    </ul>
  </section>

  <h2 class="section-title" style="top:2063px">BACK SIDE</h2>

  <!-- back side -->
  <section class="card card--back" style="top:2123px">
    <div class="card-texture" role="img" aria-label="Faint pixel-creature pattern background"></div>
    <div class="accent accent--white" style="left:0;top:0;width:40px;height:63px"></div>
    <div class="accent accent--cyan" style="left:40px;top:0;width:611px;height:40px"></div>
    <div class="accent accent--cyan" style="left:1015px;top:434px;width:34px;height:175px"></div>
    <div class="accent accent--white" style="left:1049px;top:534px;width:9px;height:75px"></div>

    <p class="offer-heading">ARE YOU INTERESTED IN?</p>
    <ul class="offer-list">
      <li>Starting your in Business?</li>
      <li>Investing in hot Startups?</li>
      <li>Working for the next "Kinloop"?</li>
    </ul>
    <p class="offer-join">JOIN US ON <span>KINLOOP.COM/VORTALEEN</span></p>
    <ul class="notes-list">
      <li>date and event<span class="notes-line"></span></li>
      <li>keywords,<span class="notes-line"></span></li>
      <li>follow up,<span class="notes-line"></span></li>
      <li><span class="notes-line"></span></li>
    </ul>
    <p class="company-line">VORTALEEN <span>- Lead the Way!</span></p>
    <p class="company-address">Berlin - Linden Hof 14 / 10117 Berlin / Germany<br>Silicon valley - 212 N Alder Rd / Sunnyvale / CA 94087</p>
    <p class="back-url">WWW.VORTALEEN.COM</p>
  </section>

</main>
</body>
</html>
```